Vantor Wear and Fuel is looking for a Clothing/Supplement Online Store Website!

Must be convenient, and user friendly, with vibrant colors that catch the eye!

Target Market(s)

Athletes, and Fashion Customers

Industry/Entity Type

Fitness

Coding

Coded - Design and coding required

Number of Pages Required

3 page

Font styles to use
Decorative

Colors

Designer to choose colors to be used in the design.

Requirements
Must have
• Somewhere to feature products, features to promote discounts and make announcements.
Nice to have
• My logos on each page

```html
<!DOCTYPE html>
<html lang="en">
<head>
<meta charset="utf-8">
<title>Vantor Wear and Fuel</title>
<link href="https://fonts.googleapis.com/css2?family=Lato:wght@400;700&display=swap" rel="stylesheet">
<style>
:root{
  --ink:#1f1f1f;
  --dark:#1e1e1e;
  --footer:#383838;
  --nav:#e9e9ea;
  --teal:#23a08b;
  --teal-deep:#1b8a78;
  --grey:#6d6d6d;
  --line:#d9d9d9;
  --white:#ffffff;
  --star:#f0652f;
}
*{box-sizing:border-box;margin:0;padding:0}
html,body{width:1200px;height:2830px;overflow:hidden}
body{position:relative;font-family:'Lato',sans-serif;color:var(--ink);background:var(--white)}
.abs{position:absolute}
.topbar{left:0;top:0;width:1200px;height:89px;background:var(--dark);color:var(--white)}
.call{left:119px;top:30px;display:flex;align-items:center;gap:10px;font-size:16px}
.call strong{font-size:21px;font-weight:700}
.brand{left:0;width:1200px;top:24px;text-align:center;font-size:22px;font-weight:700;letter-spacing:3px;color:var(--white)}
.brand i{display:block;width:16px;height:16px;background:var(--white);margin:0 auto 6px;border-radius:50%}
.cart{left:1056px;top:34px}
.navbar{left:0;top:89px;width:1200px;height:87px;background:var(--nav)}
.nav{left:109px;top:122px;display:flex;gap:0;font-size:13px;font-weight:700;align-items:center}
.nav span{margin-right:30px}
.nav .on{background:var(--dark);color:var(--white);padding:8px 7px}
.nav-right{top:127px;font-size:13px;font-weight:700}
.photo{background:linear-gradient(135deg,#9cc4bd,#6f7b72 45%,#2e3442)}
.hero-main{left:111px;top:207px;width:635px;height:446px}
.hero-text{left:136px;top:405px;color:var(--white)}
.hero-text h1{font-size:27px;font-weight:400;letter-spacing:.3px}
.hero-text p{font-size:21px;text-decoration:underline;line-height:30px;margin-top:8px}
.btn-out{display:inline-block;border:2px solid var(--white);color:var(--white);font-size:15px;padding:14px 27px}
.promo-teal{left:754px;top:207px;width:335px;height:143px;background:var(--teal);color:var(--white)}
.promo-tees{left:754px;top:357px;width:335px;height:143px;background:linear-gradient(90deg,#ececec,#d8d8d8)}
.promo-fuel{left:754px;top:507px;width:335px;height:143px;background:linear-gradient(120deg,#5a5a58,#2b2a28 60%,#b24a3a)}
.badge{left:1046px;top:355px;width:91px;height:90px;background:var(--dark);color:var(--white);clip-path:polygon(0 0,100% 0,100% 100%,0 82%)}
.perks{left:0;top:757px;width:1200px;height:73px;background:var(--dark);color:var(--white)}
.perk{top:13px;display:flex;gap:20px;align-items:center;font-size:14px;line-height:23px}
.perk b{font-weight:400;display:block}
h2.section{font-size:33px;font-weight:400}
.card{border:1px solid var(--line);background:var(--white)}
.sale-circle{left:45px;top:14px;width:111px;height:111px;border-radius:50%;background:var(--teal);color:var(--white);text-align:center}
.offer{width:239px;height:172px;color:var(--white);text-align:center;font-size:16px;display:flex;align-items:center;justify-content:center;flex-direction:column;line-height:25px}
.offer big{font-size:21px}
.newsletter{left:112px;top:1328px;width:214px;height:300px;background:#f1f1f1;text-align:center;box-shadow:0 1px 4px rgba(0,0,0,.15)}
.prod-img{width:239px;height:172px;border-radius:4px}
.prod-name{width:239px;text-align:center;font-size:16px}
.prod-price{width:239px;text-align:center;font-size:22px;color:var(--teal)}
.buy{width:123px;height:39px;border:2px solid var(--teal-deep);font-size:16px;display:flex;align-items:center;justify-content:center}
.stars{color:var(--star);font-size:19px;letter-spacing:1px}
.next{width:36px;height:36px;border:1.5px solid var(--ink);border-radius:50%;display:flex;align-items:center;justify-content:center}
.testimonial{left:112px;top:1675px;width:214px;height:263px;border:2px solid var(--teal)}
.blog{width:245px;height:380px;border:1px solid var(--line)}
.blog .img{left:8px;top:8px;width:227px;height:163px}
.date{right:8px;top:8px;width:63px;height:52px;background:var(--white);font-size:16px;text-align:center;line-height:25px;padding-top:2px}
.blog h3{left:11px;top:186px;font-size:16px;font-weight:400;line-height:26px;width:225px}
.blog p{left:11px;top:248px;font-size:16px;color:var(--grey);line-height:25px;width:228px}
.blog .more{left:12px;top:335px;font-size:16px;display:flex;gap:10px;align-items:center}
.footer{left:0;top:2354px;width:1200px;height:476px;background:var(--footer);color:var(--white)}
.footer h4{font-size:16px;font-weight:400}
.f-text{font-size:16px;line-height:26px}
.social{display:flex;align-items:center;gap:9px;font-size:16px;margin-bottom:7px}
.social i{width:32px;height:32px;border:1.5px solid var(--white);border-radius:50%;display:block}
.pay{width:46px;height:26px;border-radius:3px}
</style>
</head>
<body>

<header class="abs topbar">
  <div class="abs call">
    <svg width="28" height="28" viewBox="0 0 28 28"><circle cx="14" cy="14" r="13" fill="none" stroke="#fff" stroke-width="1.2"/><path d="M10 8c-1 1-1 3 1 6s4 5 6 5l1.5-1.5-2.5-2-1.2 1c-1-.5-2.3-2-2.8-3l1-1.2-2-2.5z" fill="none" stroke="#fff" stroke-width="1.1"/></svg>
    <span>CALL NOW - <strong>555-014-2290</strong></span>
  </div>
  <div class="abs brand"><i></i>VANTOR</div>
  <svg class="abs cart" width="26" height="26" viewBox="0 0 26 26"><path d="M2 5h4l3 11h11l3-8H7" fill="none" stroke="#fff" stroke-width="1.5"/><circle cx="10" cy="20" r="1.6" fill="#fff"/><circle cx="19" cy="20" r="1.6" fill="#fff"/><circle cx="22" cy="5" r="5" fill="#fff"/><text x="22" y="7.5" font-size="7" text-anchor="middle" fill="#000" font-family="Lato">0</text></svg>
</header>

<nav class="abs navbar"></nav>
<div class="abs nav">
  <span class="on">HOME</span>
  <span>CATEGORIES &#8964;</span>
  <span>PRODUCTS</span>
  <span>PAGES</span>
  <span>FEATURES</span>
</div>
<div class="abs nav-right" style="left:858px">SPECIAL OFFER</div>
<div class="abs nav-right" style="left:999px">BUY VANTOR</div>

<section>
  <div class="abs hero-main photo" role="img" aria-label="Athlete drinking from a shaker bottle on outdoor stairs"></div>
  <div class="abs hero-text">
    <h1>VANTOR WEAR AND FUEL</h1>
    <p>Upto 40% offer Vantor<br>supplementary</p>
    <div style="margin-top:16px;margin-left:-2px"><span class="btn-out">SHOP NOW</span></div>
  </div>

  <div class="abs promo-teal">
    <div class="abs" role="img" aria-label="Smiling woman in an orange top" style="left:200px;top:0;width:135px;height:143px;background:linear-gradient(180deg,#2bb09a,#e86a2a)"></div>
    <div class="abs" style="left:35px;top:22px;font-size:14px;font-weight:700;line-height:26px">NEW TRENDS FOR<br>WOMENS</div>
    <div class="abs" style="left:37px;top:82px;border:2px solid #fff;padding:7px 10px;font-size:14px;font-weight:700">SHOP NOW</div>
  </div>
  <div class="abs promo-tees" role="img" aria-label="Black and white basic t-shirts on hangers">
    <div class="abs" style="left:106px;top:14px;font-size:21px;color:var(--ink)">T-SHIRTS</div>
  </div>
  <div class="abs badge">
    <div class="abs" style="left:12px;top:10px;font-size:17px">UPTO</div>
    <div class="abs" style="left:20px;top:34px;font-size:16px">40%</div>
    <div class="abs" style="left:51px;top:50px;font-size:15px">offer</div>
  </div>
  <div class="abs promo-fuel" role="img" aria-label="Protein powder scoop and shaker">
    <div class="abs" style="left:0;width:335px;top:62px;text-align:center;color:#fff;font-size:14px;font-weight:700">NUTRITION COLLECTIONS</div>
  </div>
</section>

<section class="abs perks">
  <div class="abs perk" style="left:111px">
    <svg width="42" height="34" viewBox="0 0 42 34" fill="none" stroke="#23a08b" stroke-width="1.5"><rect x="2" y="6" width="24" height="18"/><path d="M26 12h8l6 7v5H26z"/><circle cx="10" cy="27" r="3"/><circle cx="33" cy="27" r="3"/></svg>
    <div><b>FREE SHIPPING &amp; RETURN</b>Free shipping on all orders over $49.</div>
  </div>
  <div class="abs perk" style="left:496px">
    <svg width="40" height="34" viewBox="0 0 40 34" fill="none" stroke="#23a08b" stroke-width="1.5"><rect x="2" y="10" width="32" height="18"/><circle cx="18" cy="19" r="5"/><path d="M6 6h32v18"/></svg>
    <div><b>MONEY BACK GUARANTEE</b>100% money back guarantee</div>
  </div>
  <div class="abs perk" style="left:869px">
    <svg width="34" height="34" viewBox="0 0 34 34" fill="none" stroke="#23a08b" stroke-width="1.5"><path d="M28 12A13 13 0 1 0 17 30"/><path d="M11 16l4 4 8-9"/><text x="20" y="32" font-size="10" fill="#23a08b" stroke="none" font-family="Lato">24</text></svg>
    <div><b>ONLINE SUPPORT 24/7</b>Lorem ipsum dolor sit amet.</div>
  </div>
</section>

<h2 class="abs section" style="left:0;width:1200px;text-align:center;top:924px">VANTOR OFFERS</h2>

<aside class="abs card" style="left:112px;top:982px;width:214px;height:301px">
  <div class="abs sale-circle">
    <div style="width:6px;height:6px;background:#fff;border-radius:50%;margin:14px auto 6px"></div>
    <div style="font-size:21px">SALE</div>
    <div style="font-size:12px;line-height:15px;margin-top:4px">Clothing &amp;<br>Nutrition</div>
  </div>
  <div class="abs" style="left:46px;top:138px;color:var(--teal);font-size:41px">40%<span style="font-size:15px;color:var(--ink)">Off</span></div>
  <div class="abs" style="left:8px;width:198px;top:193px;text-align:center;font-size:15px;line-height:21px">Lorem ipsum dolor sit amet, consectetur adipiscing elit, sed do eiusmod</div>
  <svg class="abs" style="left:74px;top:264px" width="48" height="22"><circle cx="10" cy="10" r="9" fill="none" stroke="#444"/><circle cx="10" cy="10" r="3" fill="#444"/><circle cx="36" cy="10" r="9" fill="none" stroke="#444"/></svg>
</aside>

<div class="abs offer photo" style="left:344px;top:1021px" role="img" aria-label="Man in a white t-shirt on a city street">
  <div style="margin-left:-80px">MENS<br>T-SHIRT <big>20%</big> OFF</div>
</div>
<div class="abs offer" style="left:597px;top:1021px;background:linear-gradient(120deg,#4a4a4a,#151515)" role="img" aria-label="Supplement tub beside dumbbells">
  <div>VANTOR<br>NUTRITION. <big>28%</big> OFF</div>
</div>
<div class="abs" style="left:590px;top:1012px;width:44px;height:44px;border-radius:50%;background:#e4262f;color:#fff;font-size:9px;font-weight:700;text-align:center;line-height:11px;padding-top:11px;transform:rotate(-15deg)">SPECIAL<br>OFFER</div>
<div class="abs offer" style="left:850px;top:1021px;background:#f3f3f3;box-shadow:0 1px 4px rgba(0,0,0,.15)">
  <div style="border:2px solid var(--teal);width:218px;height:157px;border-radius:3px;display:flex;flex-direction:column;justify-content:center;color:var(--ink)">
    <span style="color:var(--teal)">"VANTOR 123"</span>USE PROMO CODE<br>GET 35% OFFER
  </div>
</div>

<h2 class="abs section" style="left:348px;top:1289px">FEATURED PRODUCTS</h2>

<aside class="abs newsletter">
  <div style="font-size:16px;margin-top:46px">NEWSLETTER</div>
  <div style="font-size:16px;line-height:26px;margin:11px 26px 0">Lorem ipsum dolor sit amet,consecteturing elit</div>
  <div style="margin:13px 8px 0;height:40px;background:#fff;border:1px solid var(--line);display:flex;align-items:center;gap:10px;padding-left:14px;font-size:12px">
    <svg width="14" height="11"><rect x=".5" y=".5" width="13" height="10" fill="none" stroke="#333"/><path d="M.5 .5l6.5 6 6.5-6" fill="none" stroke="#333"/></svg>Enter your email</div>
  <div style="margin:6px 8px 0;height:41px;background:var(--teal);color:#fff;font-size:16px;display:flex;align-items:center;justify-content:center">SUBSCRIBE NOW</div>
</aside>

<div class="abs prod-img photo" style="left:344px;top:1384px" role="img" aria-label="White t-shirt with the store name"></div>
<div class="abs prod-img" style="left:596px;top:1384px;background:linear-gradient(135deg,#c9c9c9,#6b6b6b)" role="img" aria-label="Woman at the gym holding a supplement tub"></div>
<div class="abs prod-img" style="left:848px;top:1384px;background:linear-gradient(180deg,#3a1e22,#1b1b1b)" role="img" aria-label="Dark athletic pants">
  <div style="text-align:center;margin-top:52px;color:#fff;font-size:22px;text-decoration:line-through">$19:00</div>
  <div style="text-align:center;color:var(--teal);font-size:22px;margin-top:6px">$15:00</div>
</div>
<div class="abs prod-name" style="left:344px;top:1571px">T-SHIRT</div>
<div class="abs prod-name" style="left:596px;top:1571px">NUTRITION</div>
<div class="abs prod-name" style="left:848px;top:1571px">PANTS</div>
<div class="abs prod-price" style="left:344px;top:1602px">$19:00</div>
<div class="abs prod-price" style="left:596px;top:1602px">$19:00</div>
<div class="abs prod-price" style="left:848px;top:1602px">$19:00</div>
<div class="abs buy" style="left:344px;top:1650px">BUY NOW</div>
<div class="abs stars" style="left:491px;top:1653px">★★★★★</div>
<div class="abs buy" style="left:596px;top:1650px">BUY NOW</div>
<div class="abs stars" style="left:743px;top:1653px">★★★★★</div>
<div class="abs buy" style="left:848px;top:1650px">BUY NOW</div>
<div class="abs stars" style="left:995px;top:1653px">★★★★★</div>
<div class="abs next" style="left:1131px;top:1521px"><svg width="12" height="18"><path d="M2 1l8 8-8 8" fill="none" stroke="#222" stroke-width="1.5"/></svg></div>

<aside class="abs testimonial">
  <div class="abs" role="img" aria-label="Customer portrait" style="left:8px;top:30px;width:52px;height:52px;border-radius:50%;background:linear-gradient(135deg,#c9a58a,#6a5a50)"></div>
  <div class="abs" style="left:74px;top:47px;font-size:16px">MARA LIND</div>
  <div class="abs" style="left:6px;width:200px;top:114px;text-align:center;font-size:16px;line-height:26px"><span style="color:var(--teal)">“</span>Sed ut perspiciatis unde omnis iste natus error sit accusantium <span style="color:var(--teal)">„</span></div>
  <svg class="abs" style="left:80px;top:222px" width="40" height="18"><circle cx="9" cy="9" r="7.5" fill="none" stroke="#333"/><circle cx="9" cy="9" r="3.5" fill="#333"/><circle cx="30" cy="9" r="7.5" fill="none" stroke="#333"/></svg>
</aside>

<h2 class="abs section" style="left:348px;top:1782px">LATEST BLOGS</h2>

<article class="abs blog" style="left:342px;top:1869px">
  <div class="abs img" style="background:linear-gradient(135deg,#8a6a55,#4c5a6e)" role="img" aria-label="Woman in a grey cardigan"></div>
  <div class="abs date">05-Oct<br>2019</div>
  <h3 class="abs">LOREM IPSUM DOLOR SIT AMET</h3>
  <p class="abs">Sed ut perspiciatis unde omnis natus error sit&nbsp; accusantium doloremque</p>
  <div class="abs more">READ MORE <svg width="18" height="12"><path d="M1 6h15M11 1l5 5-5 5" fill="none" stroke="#222" stroke-width="1.6"/></svg></div>
</article>
<article class="abs blog" style="left:591px;top:1869px">
  <div class="abs img" style="background:linear-gradient(135deg,#c9c9c9,#3a3a3a 60%,#8a4a2a)" role="img" aria-label="Supplements and dumbbells"></div>
  <div class="abs date">05-Oct<br>2019</div>
  <h3 class="abs">LOREM IPSUM DOLOR SIT AMET</h3>
  <p class="abs">Sed ut perspiciatis unde omnis natus error sit&nbsp; accusantium doloremque</p>
  <div class="abs more">READ MORE <svg width="18" height="12"><path d="M1 6h15M11 1l5 5-5 5" fill="none" stroke="#222" stroke-width="1.6"/></svg></div>
</article>
<article class="abs blog" style="left:840px;top:1869px">
  <div class="abs img" style="background:linear-gradient(135deg,#2f55b8,#e6b9b9 55%,#c9a878)" role="img" aria-label="Woman in a pink jacket on steps"></div>
  <div class="abs date">05-Oct<br>2019</div>
  <h3 class="abs">LOREM IPSUM DOLOR SIT AMET</h3>
  <p class="abs">Sed ut perspiciatis unde omnis natus error sit&nbsp; accusantium doloremque</p>
  <div class="abs more">READ MORE <svg width="18" height="12"><path d="M1 6h15M11 1l5 5-5 5" fill="none" stroke="#222" stroke-width="1.6"/></svg></div>
</article>
<div class="abs next" style="left:1131px;top:2053px"><svg width="12" height="18"><path d="M2 1l8 8-8 8" fill="none" stroke="#222" stroke-width="1.5"/></svg></div>

<footer class="abs footer">
  <h4 class="abs" style="left:111px;top:57px">CONTACT US</h4>
  <div class="abs f-text" style="left:115px;top:92px;width:230px">ADDRESS:<br>48 Harbor Lane, Eastfield</div>
  <div class="abs f-text" style="left:115px;top:172px">PHONE:<br>Toll Free 555-014-2290</div>
  <div class="abs f-text" style="left:115px;top:240px">EMAIL:<br>hello@vantorwear.com</div>
  <div class="abs" style="left:111px;top:337px;width:202px;height:1px;background:#777"></div>
  <div class="abs pay" style="left:170px;top:324px;width:80px;height:22px;background:#2b6cb0"></div>
  <div class="abs pay" style="left:113px;top:356px;background:#3a5fb0"></div>
  <div class="abs pay" style="left:164px;top:356px;background:#e0732b"></div>
  <div class="abs pay" style="left:214px;top:356px;background:#d9d9d9"></div>
  <div class="abs pay" style="left:264px;top:356px;background:#2f7ac4"></div>
  <div class="abs f-text" style="left:117px;top:411px">© 2019 All Rights Reserved</div>

  <h4 class="abs" style="left:463px;top:57px">SUBSCRIBE NEWSLETTER</h4>
  <div class="abs f-text" style="left:463px;top:92px">Sed ut perspiciatis unde omnis<br>iste natus error sit voluptatem</div>
  <div class="abs" style="left:712px;top:98px;width:245px;height:39px;background:#fff;color:var(--ink);font-size:16px;padding:9px 10px">Enter email</div>
  <div class="abs" style="left:960px;top:98px;width:125px;height:39px;background:var(--teal);font-size:16px;text-align:center;line-height:39px">SUBSCRIBE</div>
  <div class="abs" style="left:457px;top:182px;width:632px;height:1px;background:#555"></div>

  <h4 class="abs" style="left:465px;top:232px">MY ACCOUNT</h4>
  <div class="abs f-text" style="left:466px;top:265px">Home<br>Categories<br>Products<br>Pages<br>Features<br>Blogs<br>Contact</div>
  <div class="abs f-text" style="left:656px;top:265px">Features<br>Blogs<br>Contact</div>

  <h4 class="abs" style="left:819px;top:232px">CONNECT WITH US</h4>
  <div class="abs" style="left:825px;top:266px">
    <div class="social"><i></i>Pulsebook</div>
    <div class="social"><i></i>Snapframe</div>
    <div class="social"><i></i>Chirper</div>
    <div class="social"><i></i>Workring</div>
  </div>
</footer>

</body>
</html>
```